ORV Web Design Project

I'm looking for a small, friendly,functional, information based website. If you go through the attachments, you would know the nature of the business.
Updates

Hi,

I have uploaded a picture of the CEO, Mr. Delvan Kroth PLMAT member. Please feel free to use it whereever appropriate.

Thanks!

Hello, I have uploaded some references. I like the colours used on the bar and would w

Example of a we page . I like this layout for the inside pages.

I am changing the tabs on my website to:

Home
About us
Services
Contact us

The services tab will have three sub pages:

Immigration
Education
AccommodationAccommodation

Target Market(s)

Young international students willing to come to Canada to study, young international students willing to immigrate to Canada, parents of the students

Industry/Entity Type

Business

Requirements
Must have
• ORV HOME
ABOUT US
CONTACT
SERVICES
TAG LINE

The website should look n feel trendy, smart, current, factual, trustworthy etc....
Nice to have
• I am looking for a bold, attractive, eye catchy home page with less text! Something that makes a statement....
Should not have
• No Clip art, flash animation, no bells n whistles please

```html
<!DOCTYPE html>
<html lang="en">
<head>
<meta charset="utf-8">
<title>ORV – Orvane Business Group</title>
<link href="https://fonts.googleapis.com/css2?family=Open+Sans:wght@300;400;600;700&family=Oswald:wght@400;500&family=Playball&family=Arimo:wght@400;700&display=swap" rel="stylesheet">
<style>
:root{
  --red:#e8161e;
  --red-dark:#b5121a;
  --nav:#2f2f2f;
  --ink:#222222;
  --grey:#555555;
  --grey-light:#8a8a8a;
  --line:#d8d8d8;
  --panel:#f2f2f2;
  --white:#ffffff;
}
*{margin:0;padding:0;box-sizing:border-box}
html,body{width:1106px;height:1200px;overflow:hidden;background:var(--white)}
body{position:relative;font-family:"Open Sans",Arial,sans-serif;color:var(--ink)}
.abs{position:absolute}

/* navigation */
.topbar{left:0;top:0;width:1106px;height:42px;background:var(--nav)}
.nav{left:170px;top:0;height:42px;display:flex;align-items:center;font-family:"Oswald",sans-serif;font-size:15px;letter-spacing:1px;color:#e6e6e6}
.nav a{color:inherit;text-decoration:none;height:42px;line-height:42px;padding:0 13px}
.nav a.active{background:var(--red);color:var(--white);padding:0 13px}
.nav .sep{color:var(--red);padding:0 2px;font-size:14px}
.lang{left:727px;top:14px;font-family:Arimo,sans-serif;font-size:10px;color:#fff;display:flex;align-items:center;gap:6px}
.lang .flag{width:15px;height:10px;background:#9aa4c4}
.lang .caret{width:0;height:0;border-left:5px solid transparent;border-right:5px solid transparent;border-top:5px solid #fff}
.social{display:flex;gap:8px}
.social span{width:20px;height:20px;border-radius:50%;background:#f0f0f0}
.top-social{left:818px;top:10px}

/* hero */
.hero{left:0;top:42px;width:1106px;height:445px;background:radial-gradient(ellipse at 30% 20%,#ffffff 0%,#f4f4f4 45%,#d9d9d9 100%)}
.hero-map{left:740px;top:70px;width:366px;height:400px;background:radial-gradient(ellipse at 50% 50%,rgba(240,160,160,.45),rgba(255,255,255,0) 70%)}
.hero-photo{left:558px;top:50px;width:390px;height:437px;background:linear-gradient(180deg,#d9a36a 0%,#e2b89c 22%,#9fb1cf 45%,#2a2a2e 70%,#1c1c1f 100%);border-radius:160px 160px 0 0}
.logo{left:172px;top:82px;display:flex;align-items:flex-start;gap:10px;color:#333;font-weight:700}
.logo .mark{width:22px;height:22px;background:var(--red);margin-top:12px}
.logo .abbr{font-size:52px;line-height:52px;letter-spacing:-1px}
.logo .full{font-size:25px;line-height:30px;letter-spacing:-.5px}
.tagline{left:170px;top:196px;font-family:"Playball",cursive;font-size:46px;color:#111}
.hero-copy{left:172px;top:274px;width:370px;font-size:16px;line-height:24px;font-weight:400;color:#333}
.btn-more{left:170px;top:410px;width:152px;height:40px;background:var(--red);border-radius:4px;display:flex;align-items:center;gap:10px;padding-left:8px;color:#fff;font-size:16px;font-weight:300}
.btn-more .plus{width:28px;height:28px;border-radius:50%;background:#2a2a2a;border:2px solid #fff;color:#fff;font-size:15px;line-height:22px;text-align:center;font-weight:700}

/* intro strip */
.section-title{left:0;top:504px;width:1106px;text-align:center;font-size:36px;font-weight:300;color:#222}
.section-sub{left:0;top:553px;width:1106px;text-align:center;font-size:14.5px;color:#555}
.shadow-rule{left:130px;top:598px;width:800px;height:24px;background:radial-gradient(ellipse at 50% 0%,rgba(0,0,0,.22) 0%,rgba(0,0,0,0) 65%)}

/* columns */
.col-title{font-size:23px;font-weight:400;color:#222;letter-spacing:.5px}
.body-small{font-family:Arimo,sans-serif;font-size:10.3px;line-height:15.6px;color:#555}
.welcome{left:151px;top:642px;width:250px}
.welcome .body-small{margin-top:10px}
.btn-small{display:inline-block;background:var(--red-dark);color:#fff;font-family:Arimo,sans-serif;font-size:10px;padding:2px 9px;border:1px solid #7a0a0f;margin-top:10px}
.intro{left:414px;top:638px}
.video{left:414px;top:676px;width:274px;height:160px;background:linear-gradient(160deg,#b9b2b4 0%,#8a8690 40%,#5c5964 75%,#3d3b42 100%);border:2px solid #333}
.video .play{left:120px;top:60px;width:36px;height:36px;border-radius:50%;background:rgba(255,255,255,.35)}
.video .play:after{content:"";position:absolute;left:14px;top:10px;border-left:12px solid #fff;border-top:8px solid transparent;border-bottom:8px solid transparent}
.events{left:720px;top:638px;width:215px}
.event{left:720px;width:215px;display:flex;gap:6px}
.event .date{width:32px;height:38px;background:var(--red);color:#fff;text-align:center;font-weight:700;line-height:1}
.event .date b{display:block;font-size:15px;padding-top:4px}
.event .date i{display:block;font-style:normal;font-size:9px;padding-top:2px}
.event .body-small{font-size:9.6px;line-height:12px;flex:1}
.event-1{top:678px}
.event-2{top:758px}
.event-rule{left:722px;top:742px;width:175px;height:1px;background:var(--line)}
.btn-events{left:717px;top:834px}

/* partners */
.partners{left:154px;top:886px;width:780px;height:68px;background:var(--panel);border:1px solid #dcdcdc}
.arrow{top:17px;width:30px;height:30px;border-radius:50%;background:var(--red)}
.arrow svg{display:block}
.arrow-left{left:8px}
.arrow-right{right:12px}
.badge{top:20px;height:26px;background:#9c9c9c;border-radius:3px}
.partners-shadow{left:130px;top:954px;width:830px;height:22px;background:radial-gradient(ellipse at 50% 0%,rgba(0,0,0,.18) 0%,rgba(0,0,0,0) 65%)}

/* footer */
.newsletter{left:154px;top:1024px;width:236px;height:116px;border:1px solid #dadada;background:#fff}
.newsletter-head{left:-1px;top:-1px;width:238px;height:36px;background:var(--red);color:#fff;font-family:"Oswald",sans-serif;font-size:18px;line-height:36px;padding-left:20px;text-transform:uppercase}
.newsletter label{position:absolute;left:20px;top:46px;font-family:Arimo,sans-serif;font-size:10px;color:#333}
.newsletter .field{position:absolute;left:20px;top:61px;width:182px;height:26px;border:1px solid #cfcfcf}
.newsletter .submit{position:absolute;left:148px;top:90px;width:56px;height:18px;background:#e0e0e0;border:1px solid #aaa;font-family:"Oswald",sans-serif;font-size:11px;text-align:center;line-height:16px}
.contact-title{left:433px;top:1026px;font-family:"Oswald",sans-serif;font-size:19px;font-weight:500;color:#111}
.footer-social{left:528px;top:1028px}
.footer-social span{background:#1a1a1a}
.contact-list{left:434px;top:1066px;font-family:Arimo,sans-serif;font-size:9.8px;line-height:16.5px;color:#c8141b}
.contact-list b{color:#111}
.footer-logo{left:758px;top:1036px;display:flex;align-items:center;gap:10px;color:#1a1a1a;font-weight:700;font-size:56px;letter-spacing:-1px}
.footer-logo .mark{width:22px;height:22px;background:var(--red)}
.copyright{left:664px;top:1118px;font-family:Arimo,sans-serif;font-size:10.5px;color:#222}
.bottom-band{left:0;top:1162px;width:1106px;height:38px;background:var(--red)}
</style>
</head>
<body>

<header class="abs topbar"></header>
<nav class="abs nav">
  <a class="active">HOME</a><span class="sep">/</span>
  <a>ABOUT US</a><span class="sep">/</span>
  <a>CONTACT</a><span class="sep">/</span>
  <a>SERVICES</a>
</nav>
<div class="abs lang"><span class="flag"></span>English<span class="caret"></span></div>
<div class="abs social top-social"><span></span><span></span><span></span><span></span></div>

<section class="abs hero"></section>
<div class="abs hero-map" role="img" aria-label="Faint map of eastern Canada in soft red"></div>
<div class="abs hero-photo" role="img" aria-label="Photograph of a businesswoman in a dark suit holding a folder"></div>

<div class="abs logo">
  <span class="mark"></span>
  <div><div class="abbr">ORV</div><div class="full">Orvane Business Group</div></div>
</div>
<div class="abs tagline">Taking you onwards.....</div>
<p class="abs hero-copy">Delvan Kroth, CEO of Orvane Business Group, has vast knowledge in the field of Student Recruitment &amp; Higher Education. He is an MBA from Canada and is very well known in the India-Canada education corridor since 2004.</p>
<div class="abs btn-more"><span class="plus">+</span>Learn More</div>

<h1 class="abs section-title">Student Recruitment &amp; Higher Education</h1>
<p class="abs section-sub">Mr. Kroth contributed significantly towards Northbay College’s immense growth of international students from his region.</p>
<div class="abs shadow-rule"></div>

<section class="abs welcome">
  <h2 class="col-title">WELCOME</h2>
  <p class="body-small">Lorem ipsum dolor sit amet, consectetuer adipiscing elit, sed diam nonummy nibh euismod tincidunt ut laoreet dolore magna aliquam erat volutpat. Ut wisi enim ad minim veniam, quis nostrud exerci tation ullamcorper suscipit lobortis nisl ut aliquip ex ea commodo consequat.<br>Duis autem vel eum iriure dolor in hendrerit in vulputate velit esse molestie consequat, vel illum dolore eu feugiat nulla facilisis at vero eros et accumsan ..</p>
  <span class="btn-small">Read More</span>
</section>

<h2 class="abs col-title intro">INTRODUCTION</h2>
<div class="abs video" role="img" aria-label="Video still of a business meeting around a conference table">
  <span class="abs play"></span>
</div>

<h2 class="abs col-title events">EVENTS &amp; NEWS</h2>
<div class="abs event event-1">
  <div class="date"><b>17</b><i>JAN</i></div>
  <p class="body-small">Lorem ipsum dolor sit amet, consectetuer adipiscing elit, sed diam nonummy nibh euismod tincidunt ut laoreet dolore .</p>
</div>
<div class="abs event-rule"></div>
<div class="abs event event-2">
  <div class="date"><b>15</b><i>JAN</i></div>
  <p class="body-small">Lorem ipsum dolor sit amet, consectetuer adipiscing elit, sed diam nonummy nibh euismod tincidunt ut laoreet dolore magna aliquam erat volutpat.</p>
</div>
<span class="abs btn-small btn-events">View all events</span>

<section class="abs partners" aria-label="Partners">
  <span class="abs arrow arrow-left"><svg width="30" height="30" viewBox="0 0 30 30"><path d="M17 9 L11 15 L17 21 Z" fill="#fff"/></svg></span>
  <span class="abs badge" style="left:80px;width:46px"></span>
  <span class="abs badge" style="left:170px;width:82px"></span>
  <span class="abs badge" style="left:296px;width:58px"></span>
  <span class="abs badge" style="left:396px;width:78px"></span>
  <span class="abs badge" style="left:534px;width:50px"></span>
  <span class="abs badge" style="left:624px;width:86px"></span>
  <span class="abs arrow arrow-right"><svg width="30" height="30" viewBox="0 0 30 30"><path d="M13 9 L19 15 L13 21 Z" fill="#fff"/></svg></span>
</section>
<div class="abs partners-shadow"></div>

<section class="abs newsletter">
  <div class="abs newsletter-head">Sign up for newsletter</div>
  <label>Email Address</label>
  <span class="field"></span>
  <span class="submit">SUBMIT</span>
</section>

<h3 class="abs contact-title">CONTACT</h3>
<div class="abs social footer-social"><span></span><span></span><span></span><span></span></div>
<address class="abs contact-list" style="font-style:normal">
  <b>Address:</b> 418 Maple Row, Brookton, Ontario,<br>K2P 3J7 Canada<br>
  <b>Phone:</b> (555) 010 4821 (555) 010 7390<br>
  <b>Email:</b>info@orvanegroup.com
</address>

<div class="abs footer-logo"><span class="mark"></span>ORV</div>
<p class="abs copyright">© 2013 Orvane Business Group. All Rights Reserved</p>

<footer class="abs bottom-band"></footer>

</body>
</html>
```